Letterhead and matching envelope design for a dental office

We need a new stationary design, letterhead and envelope #10, for a dental office in Denver area. We are called Bright Harbor Dental. We want a simple and minimalistic design but not a boring design. I wish to have one good point that makes it look professional. I have attached our logo. Feel free to use either one. I want the design for letterhead and envelope look like a "matching pair" but not look the same. The envelope doesn't have to be white and it will have an address window on bottom left.

Target Market(s)

everyone who visits dentist (adults)

Industry/Entity Type

Dental

Font styles to use
Other font styles liked:
• close to font on logo or something that matches well

Requirements
Must have
• professional
• simple, minimalistic
• unique point that stands out
Nice to have
• matching but not same design for letterhead and envelope
Should not have
• not look like all the other boring designs
• no flowery, distracting feats

```html
<!DOCTYPE html>
<html lang="en">
<head>
<meta charset="utf-8">
<title>Bright Harbor Dental — Letterhead</title>
<link rel="stylesheet" href="https://fonts.googleapis.com/css2?family=Open+Sans:wght@400;600&family=Handlee&display=swap">
<style>
  :root {
    --backdrop: #e9e9e9;
    --paper: #ffffff;
    --green: #3ab54a;
    --green-light: #b8dcb6;
    --ink: #2a2a2a;
    --ink-soft: #444444;
    --signature: #1f2a8a;
  }
  * { box-sizing: border-box; margin: 0; padding: 0; }
  html, body {
    width: 1200px; height: 876px; overflow: hidden;
    background: var(--backdrop);
    font-family: "Open Sans", Arial, sans-serif;
  }
  .letterhead {
    position: absolute; left: 310px; top: 28px;
    width: 580px; height: 820px;
    background: var(--paper);
    box-shadow: 0 2px 8px rgba(0,0,0,0.12);
    overflow: hidden;
  }
  .brand {
    position: absolute; left: 40px; top: 62px;
    display: flex; align-items: center; gap: 8px;
  }
  .brand-dot {
    width: 12px; height: 12px; border-radius: 50%;
    background: var(--green);
  }
  .brand-name {
    font-size: 14px; font-weight: 600; color: var(--green);
    letter-spacing: 0.5px;
  }
  .contact {
    position: absolute; right: 40px; top: 40px;
    font-style: normal;
    text-align: right; font-size: 9px; line-height: 1.45; color: var(--ink);
  }
  .contact-name { color: var(--green); }
  .contact-line { display: flex; justify-content: flex-end; align-items: center; gap: 4px; }
  .contact-icon { width: 9px; height: 9px; }
  .letter-body {
    position: absolute; left: 40px; top: 238px; width: 490px;
    font-size: 9.5px; line-height: 1.5; color: var(--ink-soft);
  }
  .letter-date { margin-bottom: 2px; color: var(--ink); }
  .letter-body p { margin-bottom: 12px; }
  .signature {
    position: absolute; left: 40px; top: 500px;
  }
  .signature-name {
    font-family: "Handlee", cursive; font-size: 24px; color: var(--signature);
    line-height: 1;
  }
  .signature-role { font-size: 9.5px; color: var(--ink); margin-top: 2px; }
  .swoosh { position: absolute; left: 0; bottom: 0; width: 580px; height: 260px; }
</style>
</head>
<body>
  <main class="letterhead">
    <header>
      <div class="brand">
        <span class="brand-dot"></span>
        <span class="brand-name">Bright Harbor Dental</span>
      </div>
      <address class="contact">
        <div class="contact-name">Bright Harbor Dental</div>
        <div>2815 Lakeview Blvd,</div>
        <div>Suite 210 Arvada, CO 80002</div>
        <div class="contact-line">720-555-0142
          <svg class="contact-icon" viewBox="0 0 10 10" aria-hidden="true"><circle cx="5" cy="5" r="5" fill="var(--green)"/><path d="M3.2 2.6l1 1-.5.6c.4.8 1 1.4 1.8 1.8l.6-.5 1 1-.6.8C4.7 7.2 2.8 5.3 2.4 3.2z" fill="#fff"/></svg>
        </div>
        <div class="contact-line">hello@brightharbordental.com
          <svg class="contact-icon" viewBox="0 0 10 10" aria-hidden="true"><circle cx="5" cy="5" r="5" fill="var(--green)"/><rect x="2.6" y="3.3" width="4.8" height="3.4" fill="#fff"/><path d="M2.6 3.3L5 5.2l2.4-1.9" stroke="var(--green)" stroke-width="0.6" fill="none"/></svg>
        </div>
        <div class="contact-line">www.brightharbordental.com
          <svg class="contact-icon" viewBox="0 0 10 10" aria-hidden="true"><circle cx="5" cy="5" r="5" fill="var(--green)"/><circle cx="5" cy="5" r="2.6" fill="none" stroke="#fff" stroke-width="0.6"/><path d="M2.4 5h5.2M5 2.4v5.2" stroke="#fff" stroke-width="0.6"/></svg>
        </div>
      </address>
    </header>

    <section class="letter-body">
      <div class="letter-date">Ankerrul January, 2016</div>
      <p>Lorem Ipsum is simply dummy text of the printing and typesetting industry. Lorem Ipsum has been the industry's standard dummy text ever since the 1500s, when an unknown printer took a galley of type and scrambled it to make a type specimen book. It has survived not only five centuries, but also the leap into electronic typesetting, remaining essentially unchanged. It was popularised in the 1960s with the release of Dryline sheets containing Lorem Ipsum passages, and more recently with desktop publishing software like Inkwell Layout including versions of Lorem Ipsum.</p>
      <p>The standard chunk of Lorem Ipsum used since the 1500s is reproduced below for those interested. Sections 1.10.32 and 1.10.33 from "de Rebus Variis et Communibus" by Velarius are also reproduced in their exact original form, accompanied by English versions from the 1914 translation by J. Halloway</p>
      <p>Lorem Ipsum is simply dummy text of the printing and typesetting industry. Lorem Ipsum has been the industry's standard dummy text ever since the 1500s, when an unknown printer took a galley of type and scrambled it to make a type specimen book. It has survived not only five centuries, but also the leap into electronic typesetting, remaining essentially unchanged. It was popularised in the</p>
    </section>

    <div class="signature">
      <div class="signature-name">your name</div>
      <div class="signature-role">Company Director</div>
    </div>

    <svg class="swoosh" viewBox="0 0 580 260" preserveAspectRatio="none" aria-hidden="true">
      <path d="M0 260 C180 230 420 130 580 20 L580 34 C430 150 220 245 70 260 Z" fill="var(--green-light)"/>
      <path d="M110 260 C290 215 460 125 580 48 L580 120 C470 185 330 240 240 260 Z" fill="var(--green)"/>
      <path d="M380 260 C460 230 530 195 580 168 L580 190 C535 218 480 245 440 260 Z" fill="var(--green-light)"/>
    </svg>
  </main>
</body>
</html>
```